8x8 Social Media Ad - Brant Summit Expo

Attention Real Estate Agents
Please join us for our
Quarterly Real Estate Training Expo
The 2nd Saturday of February, May, August and November
Our Next Training Expo is _________________________________
From 9 am to 1 pm
at
Halvorne Suites Millbrook Court
4817 Copper Willow Lane, Dunmere, MD 20588
Scheduled Speakers
9:00 am - Marcus Pellington - Orientation
9:30 am - Derrin Oakfield - Multiple Income Streams / Crest Program
10:00 am - Talia Brennick - Marketing though Social Media
10:45 am - Rex Dunmore - Generating Business through Ru-Plaza
11:30 am - Kemi Adeyoro - Real Estate Investing
12:15 pm - Gregor Tamsey - (Main Speaker) Training Topic TBA
For more information call Marcus Pellington at (240) 555-0183 or email mpellington@brantsummithomes.example

```html
<!DOCTYPE html>
<html lang="en">
<head>
<meta charset="utf-8">
<title>Brant Summit Expo – Quarterly Real Estate Training Expo</title>
<link rel="stylesheet" href="https://fonts.googleapis.com/css2?family=Montserrat:ital,wght@0,400;0,500;0,600;0,700;0,800;0,900;1,900&display=swap">
<style>
  :root {
    --navy: #1d3a70;
    --navy-deep: #142b58;
    --navy-light: #27488a;
    --teal: #16909b;
    --yellow: #f4e500;
    --orange: #f6a81c;
    --white: #ffffff;
    --ink: #14213d;
  }
  * { margin: 0; padding: 0; box-sizing: border-box; }
  html, body { width: 1200px; height: 1200px; overflow: hidden; background: var(--navy-deep); }
  body { font-family: "Montserrat", Arial, sans-serif; color: var(--white); }

  .ad {
    position: relative; width: 1200px; height: 1200px; overflow: hidden;
    background: radial-gradient(ellipse at 40% 40%, var(--navy-light) 0%, var(--navy) 50%, var(--navy-deep) 100%);
  }
  .edge-line { position: absolute; left: 0; width: 1200px; height: 4px; background: var(--teal); opacity: .8; }
  .edge-line.top { top: 17px; }
  .edge-line.bottom { top: 1156px; }
  .divider { position: absolute; left: 607px; top: 60px; width: 1px; height: 1080px; background: rgba(255,255,255,.18); }

  .attention { position: absolute; left: 0; top: 0; width: 610px; height: 300px; }
  .attention-label { font-family: "Montserrat", Arial, sans-serif; font-weight: 900; font-style: italic; fill: var(--white); }
  .audience { position: absolute; left: 127px; top: 236px; font-size: 43px; font-weight: 600; letter-spacing: 1px; }

  .speaker { position: absolute; width: 200px; text-align: center; }
  .speaker .photo {
    display: block; width: 166px; height: 166px; margin: 0 auto; border-radius: 50%;
    background: linear-gradient(180deg, #3a4663 0%, #2f3d5e 60%, var(--teal) 60%, var(--teal) 100%);
    box-shadow: 0 6px 14px rgba(0,0,0,.45);
  }
  .speaker .name { display: block; margin-top: 6px; font-size: 28px; font-weight: 700; letter-spacing: 1px; }

  .brand-band {
    position: absolute; left: 0; top: 916px; width: 560px; height: 193px;
    background: linear-gradient(90deg, #ffffff 0%, #ffffff 68%, rgba(255,255,255,0) 100%);
  }
  .brand {
    position: absolute; left: 70px; top: 988px; display: flex; align-items: center; gap: 14px;
    color: var(--teal); font-weight: 800; font-size: 27px; letter-spacing: .5px;
  }
  .brand .mark { width: 40px; height: 40px; background: var(--teal); }

  .invite { position: absolute; left: 646px; top: 148px; font-size: 34px; font-weight: 700; color: var(--yellow); letter-spacing: 1px; }
  .headline { position: absolute; left: 620px; top: 200px; width: 560px; height: 400px; }
  .headline text { font-family: "Montserrat", Arial, sans-serif; font-weight: 800; fill: var(--white); }

  .schedule-bar { position: absolute; left: 633px; top: 630px; width: 526px; height: 54px; display: flex; background: var(--white); }
  .schedule-bar .when {
    width: 208px; background: var(--teal); display: flex; align-items: center; justify-content: center; gap: 10px;
    font-weight: 800; font-size: 40px; color: var(--white);
  }
  .schedule-bar .when sup { font-size: 22px; vertical-align: 16px; }
  .schedule-bar .when .bar { width: 2px; height: 36px; background: var(--white); }
  .schedule-bar .months { flex: 1; display: flex; align-items: center; justify-content: center; font-size: 24px; font-weight: 500; color: var(--ink); letter-spacing: 1px; }

  .venue { position: absolute; left: 639px; top: 698px; font-size: 19px; line-height: 25px; letter-spacing: .6px; white-space: nowrap; }
  .venue .next { display: block; margin-top: 3px; }
  .venue .blank { display: inline-block; width: 84px; border-bottom: 1px solid var(--white); }

  .speakers-title { position: absolute; left: 645px; top: 790px; font-size: 28px; font-weight: 600; color: var(--teal); letter-spacing: .5px; }
  .speakers { position: absolute; left: 640px; top: 831px; width: 531px; border-collapse: collapse; border: 1px solid rgba(255,255,255,.8); font-size: 14px; }
  .speakers td { height: 21px; border-bottom: 1px solid rgba(255,255,255,.8); padding: 0 4px; white-space: nowrap; }
  .speakers .time { font-weight: 700; width: 82px; }
  .speakers .who { font-weight: 700; text-align: right; width: 122px; }
  .speakers .topic { font-weight: 400; padding-left: 18px; }

  .contact { position: absolute; left: 620px; top: 982px; width: 560px; text-align: center; white-space: nowrap; }
  .contact .lead { font-size: 21px; letter-spacing: .4px; }
  .contact .phone { display: block; margin-top: 8px; font-size: 66px; font-weight: 800; color: var(--teal); letter-spacing: 1px; line-height: 70px; }
  .contact .email { display: block; margin-top: 10px; font-size: 19px; letter-spacing: .2px; }
</style>
</head>
<body>
<main class="ad">
  <div class="edge-line top"></div>
  <div class="edge-line bottom"></div>
  <div class="divider"></div>

  <header class="attention">
    <svg width="610" height="300" viewBox="0 0 610 300" aria-hidden="true">
      <polygon points="30,78 171,75 125,261 12,262" fill="var(--teal)"/>
      <polygon points="168,92 600,74 586,222 140,238" fill="var(--orange)"/>
      <polygon points="178,100 582,84 570,210 155,226" fill="#101010"/>
      <rect x="74" y="94" width="26" height="112" rx="6" fill="#e8e8e8" transform="skewX(-8)"/>
      <circle cx="78" cy="226" r="15" fill="#e8e8e8"/>
      <text class="attention-label" x="185" y="192" font-size="66" textLength="370" lengthAdjust="spacingAndGlyphs" transform="rotate(-3 370 160)">ATTENTION</text>
    </svg>
    <div class="audience">Real Estate Agents</div>
  </header>

  <section class="speaker-grid">
    <figure class="speaker" style="left:15px;top:389px"><span class="photo" role="img" aria-label="Portrait of Derrin"></span><figcaption class="name">DERRIN</figcaption></figure>
    <figure class="speaker" style="left:195px;top:389px"><span class="photo" role="img" aria-label="Portrait of Rex"></span><figcaption class="name">REX</figcaption></figure>
    <figure class="speaker" style="left:387px;top:389px"><span class="photo" role="img" aria-label="Portrait of Talia"></span><figcaption class="name">TALIA</figcaption></figure>
    <figure class="speaker" style="left:18px;top:656px"><span class="photo" role="img" aria-label="Portrait of Marcus"></span><figcaption class="name">MARCUS</figcaption></figure>
    <figure class="speaker" style="left:197px;top:656px"><span class="photo" role="img" aria-label="Portrait of Gregor"></span><figcaption class="name">GREGOR</figcaption></figure>
    <figure class="speaker" style="left:378px;top:656px"><span class="photo" role="img" aria-label="Portrait of Kemi"></span><figcaption class="name">KEMI</figcaption></figure>
  </section>

  <div class="brand-band"></div>
  <div class="brand"><span class="mark"></span><span>BRANT SUMMIT HOMES</span></div>

  <p class="invite">PLEASE JOIN US FOR OUR</p>
  <svg class="headline" viewBox="0 0 560 400" aria-label="Quarterly Real Estate Training Expo">
    <text x="7" y="70" font-size="80" textLength="534" lengthAdjust="spacingAndGlyphs">QUARTERLY</text>
    <text x="7" y="148" font-size="76" textLength="530" lengthAdjust="spacingAndGlyphs">REAL ESTATE</text>
    <text x="7" y="241" font-size="104" textLength="534" lengthAdjust="spacingAndGlyphs">TRAINING</text>
    <text x="10" y="387" font-size="176" textLength="530" lengthAdjust="spacingAndGlyphs">EXPO</text>
  </svg>

  <div class="schedule-bar">
    <div class="when"><span>2<sup>nd</sup></span><span class="bar"></span><span>SAT</span></div>
    <div class="months">FEB | MAY | AUG | NOV</div>
  </div>

  <p class="venue">
    Halvorne Suites Millbrook Court<br>
    4817 Copper Willow Lane, Dunmere, MD 20588
    <span class="next">Our Next Training Expo is <span class="blank"></span>-From 9 am to 1 pm</span>
  </p>

  <h2 class="speakers-title">Scheduled Speakers</h2>
  <table class="speakers">
    <tr><td class="time">9:00 AM</td><td class="who">Marcus Pellington</td><td class="topic">Orientation</td></tr>
    <tr><td class="time">9:30 AM</td><td class="who">Derrin Oakfield</td><td class="topic">Multiple Income Streams / Crest Program</td></tr>
    <tr><td class="time">10:00 AM</td><td class="who">Talia Brennick</td><td class="topic">Marketing though Social Media</td></tr>
    <tr><td class="time">10:45 AM</td><td class="who">Rex Dunmore</td><td class="topic">Generating Business through Ru-Plaza</td></tr>
    <tr><td class="time">11:30 AM</td><td class="who">Kemi Adeyoro</td><td class="topic">Real Estate Investing</td></tr>
    <tr><td class="time">12:15 PM</td><td class="who">Gregor Tamsey</td><td class="topic">(Main Speaker) Training Topic TBA</td></tr>
  </table>

  <footer class="contact">
    <p class="lead">For more information call Marcus Pellington at</p>
    <span class="phone">(240) 555-0183</span>
    <span class="email">or email mpellington@brantsummithomes.example</span>
  </footer>
</main>
</body>
</html>
```